Velmora Freightway Solutions Business cards

Would like a very unique design catchy but professional for business cards. Please use log provided.Marlon WellsCeo and Founder TransCon Logistix Solutions1-888-913-3225mwells@tlsolutionsus.comwww.tlsolutionsus.com

```html
<!DOCTYPE html>
<html lang="en">
<head>
<meta charset="utf-8">
<title>Velmora Freightway Solutions – Business Cards</title>
<link rel="stylesheet" href="https://fonts.googleapis.com/css2?family=Montserrat:wght@500;600;700&display=swap">
<style>
  :root {
    --brand-blue: #1273bf;
    --brand-red: #e2232a;
    --card-white: #ffffff;
    --backdrop: #e9eaed;
    --text-blue: #1c6cb5;
  }
  * { margin: 0; padding: 0; box-sizing: border-box; }
  html, body { width: 1200px; height: 800px; overflow: hidden; }
  body {
    background: var(--backdrop);
    font-family: "Montserrat", Arial, sans-serif;
    position: relative;
  }
  .card {
    position: absolute;
    width: 560px;
    height: 320px;
    overflow: hidden;
    box-shadow: 0 10px 30px rgba(0,0,0,0.18);
  }

  /* Front */
  .card-front {
    left: 60px; top: 70px;
    background: var(--brand-blue);
    color: var(--card-white);
    display: flex;
    flex-direction: column;
    align-items: center;
    justify-content: center;
    gap: 22px;
  }
  .front-brand {
    display: flex;
    align-items: center;
    gap: 12px;
  }
  .brand-square {
    width: 18px; height: 18px;
    background: var(--brand-red);
    flex: none;
  }
  .front-brand-name {
    font-weight: 700;
    font-size: 22px;
    letter-spacing: 1.5px;
    text-transform: uppercase;
    line-height: 1.25;
    text-align: left;
  }
  .front-web {
    font-weight: 500;
    font-size: 13px;
    letter-spacing: 4px;
  }

  /* Back */
  .card-back {
    left: 580px; top: 410px;
    background: var(--card-white);
  }
  .back-tab {
    position: absolute;
    right: 0; top: 50px;
    width: 18px; height: 46px;
    background: var(--brand-red);
  }
  .back-bar {
    position: absolute;
    left: 0; top: 196px;
    width: 26px; height: 58px;
    background: var(--brand-red);
  }
  .back-brand {
    position: absolute;
    left: 40px; top: 186px;
    display: flex;
    align-items: center;
    gap: 10px;
  }
  .back-brand-name {
    font-weight: 700;
    font-size: 21px;
    line-height: 1.2;
    color: var(--text-blue);
    text-transform: uppercase;
    letter-spacing: 0.5px;
  }
  .contact {
    position: absolute;
    left: 300px; top: 92px;
  }
  .contact-name {
    font-weight: 600;
    font-size: 22px;
    color: var(--text-blue);
    line-height: 1.1;
  }
  .contact-role {
    font-weight: 500;
    font-size: 14px;
    color: var(--brand-red);
    margin-bottom: 10px;
  }
  .contact-line {
    display: flex;
    align-items: center;
    gap: 7px;
    font-weight: 500;
    font-size: 12.5px;
    color: var(--text-blue);
    margin-top: 5px;
  }
  .contact-icon { width: 16px; height: 16px; flex: none; }
</style>
</head>
<body>

  <section class="card card-front" aria-label="Business card front">
    <div class="front-brand">
      <span class="brand-square"></span>
      <div class="front-brand-name">Velmora Freightway<br>Solutions</div>
    </div>
    <div class="front-web">www.vfwayroutes.com</div>
  </section>

  <section class="card card-back" aria-label="Business card back">
    <span class="back-tab"></span>
    <span class="back-bar"></span>

    <div class="back-brand">
      <div class="back-brand-name">Velmora<br>Freightway<br>Solutions</div>
    </div>

    <div class="contact">
      <div class="contact-name">Dorian Pike</div>
      <div class="contact-role">Ceo and Founder</div>
      <div class="contact-line">
        <svg class="contact-icon" viewBox="0 0 16 16" aria-hidden="true">
          <circle cx="8" cy="8" r="7.5" fill="#e2232a"/>
          <rect x="5.5" y="3.8" width="5" height="8.4" rx="1" fill="none" stroke="#fff" stroke-width="1.2"/>
          <circle cx="8" cy="10.6" r="0.6" fill="#fff"/>
        </svg>
        <span>1-888-470-6158</span>
      </div>
      <div class="contact-line">
        <svg class="contact-icon" viewBox="0 0 16 16" aria-hidden="true">
          <circle cx="8" cy="8" r="7.5" fill="#e2232a"/>
          <rect x="4" y="5" width="8" height="6" fill="none" stroke="#fff" stroke-width="1.1"/>
          <path d="M4 5 L8 8.5 L12 5" fill="none" stroke="#fff" stroke-width="1.1"/>
        </svg>
        <span>dpike@vfwayroutes.com</span>
      </div>
    </div>
  </section>

</body>
</html>
```